Business Card Design

I need a business card for a new company based in Australia called "MedLinkora".

Its a cloud program for GPs that allows them to search for the specialist they require using a simple user friendly tool.

I would like the colours to match those in the program (the colours in the logo attached).

The final design should reflect the programs clarity, ease of use and professionalism.

Target Market(s)

GPs and other Health Professionals

Industry/Entity Type

Business

Contact Information for Business Card

MedLinkora; The Whole Consultant Index; Marla Voss CEO; 0438215967; marla@medlinkora.example; www.medlinkora.example

Requirements
Must have
• Must have the logo attached; the web address and my name and phone number
Nice to have
• the slogan "The Whole Consultant Index"

```html
<!DOCTYPE html>
<html lang="en">
<head>
<meta charset="utf-8">
<title>MedLinkora Business Card</title>
<link rel="stylesheet" href="https://fonts.googleapis.com/css2?family=Open+Sans:wght@400;600;700&family=Questrial&display=swap">
<style>
  :root {
    --brand-blue: #1db4e6;
    --ink-grey: #7b7b7b;
    --ink-dark: #2e2e2e;
    --card-white: #ffffff;
    --backdrop: #e9ecef;
  }
  * { box-sizing: border-box; margin: 0; padding: 0; }
  html, body {
    width: 1200px; height: 1200px; overflow: hidden;
    background: var(--backdrop);
  }
  .stage {
    width: 1200px; height: 1200px;
    display: flex; flex-direction: column; align-items: center; justify-content: center;
    gap: 70px;
  }
  .card {
    position: relative;
    width: 880px; height: 500px;
    border-radius: 44px;
    overflow: hidden;
    box-shadow: 0 6px 22px rgba(0,0,0,0.12);
  }
  .card--front { background: var(--card-white); }
  .card--back { background: var(--brand-blue); }

  .side-bands { position: absolute; inset: 0; width: 100%; height: 100%; }
  .side-bands path { fill: var(--brand-blue); }

  .wordmark {
    font-family: "Questrial", sans-serif;
    font-size: 118px; line-height: 1; letter-spacing: -3px;
    white-space: nowrap;
  }
  .tagline {
    font-family: "Questrial", sans-serif;
    font-size: 32px; line-height: 1; letter-spacing: 0.5px;
    white-space: nowrap;
  }

  .card--front .brand { position: absolute; left: 0; right: 0; top: 58px; text-align: center; }
  .card--front .wordmark { color: var(--brand-blue); }
  .card--front .tagline { color: var(--ink-grey); margin-top: 4px; }

  .holder {
    position: absolute; left: 0; right: 0; top: 262px; text-align: center;
    font-family: "Open Sans", sans-serif; font-size: 34px;
  }
  .holder__name { color: var(--brand-blue); font-weight: 700; }
  .holder__role { color: var(--ink-grey); font-weight: 400; }

  .phone {
    position: absolute; left: 0; right: 0; top: 336px;
    display: flex; justify-content: center; align-items: center; gap: 14px;
    font-family: "Open Sans", sans-serif; font-size: 34px; color: var(--ink-dark);
  }
  .contact-line {
    position: absolute; left: 0; right: 0; top: 412px;
    display: flex; justify-content: center; align-items: center; gap: 26px;
    font-family: "Open Sans", sans-serif; font-size: 25px; color: var(--ink-dark);
  }
  .contact-item { display: flex; align-items: center; gap: 10px; }
  .icon { display: block; }
  .icon path, .icon circle, .icon rect, .icon line { stroke: var(--brand-blue); fill: none; stroke-width: 2; }
  .icon .solid { fill: var(--brand-blue); stroke: none; }

  .card--back .brand { position: absolute; left: 0; right: 0; top: 110px; text-align: center; }
  .card--back .wordmark { color: var(--card-white); font-size: 124px; }
  .card--back .tagline { color: var(--card-white); margin-top: 4px; font-size: 34px; }
  .back-url {
    position: absolute; left: 0; right: 0; top: 352px; text-align: center;
    font-family: "Open Sans", sans-serif; font-size: 34px; letter-spacing: 4px;
    color: var(--card-white);
  }
</style>
</head>
<body>
<main class="stage">

  <section class="card card--front" aria-label="Card front">
    <svg class="side-bands" viewBox="0 0 880 500" preserveAspectRatio="none" aria-hidden="true">
      <path d="M0 40 Q48 250 0 460 Z"/>
      <path d="M880 40 Q832 250 880 460 Z"/>
    </svg>
    <div class="brand">
      <div class="wordmark">MedLinkora</div>
      <div class="tagline">The Whole Consultant Index</div>
    </div>
    <p class="holder"><span class="holder__name">Marla Voss,</span> <span class="holder__role">CEO</span></p>
    <p class="phone">
      <svg class="icon" width="32" height="32" viewBox="0 0 32 32" aria-hidden="true">
        <circle cx="16" cy="16" r="14"/>
        <path class="solid" d="M11 9 l4 0 l1 4 l-2 2 q2 4 5 5 l2 -2 l4 1 l0 4 q-1 2 -3 2 q-9 -1 -13 -12 q0 -3 2 -4 Z"/>
      </svg>
      <span>0438215967</span>
    </p>
    <div class="contact-line">
      <span class="contact-item">
        <svg class="icon" width="26" height="22" viewBox="0 0 26 22" aria-hidden="true">
          <rect x="2" y="4" width="22" height="15" rx="2"/>
          <path d="M2 6 L13 13 L24 6"/>
        </svg>
        marla@medlinkora.example
      </span>
      <span class="contact-item">
        <svg class="icon" width="24" height="24" viewBox="0 0 24 24" aria-hidden="true">
          <circle cx="12" cy="12" r="10"/>
          <path d="M12 2 Q6 12 12 22 Q18 12 12 2"/>
          <line x1="2" y1="12" x2="22" y2="12"/>
        </svg>
        www.medlinkora.example
      </span>
    </div>
  </section>

  <section class="card card--back" aria-label="Card back">
    <div class="brand">
      <div class="wordmark">MedLinkora</div>
      <div class="tagline">The Whole Consultant Index</div>
    </div>
    <p class="back-url">www.medlinkora.example</p>
  </section>

</main>
</body>
</html>
```